New Website Design & Build Project - Lively Oak Dishes

I am looking for a professional clean looking website design then build of a website for my meal delivery business Lively Oak Dishes. I already have the domain - www.livelyoakdishes.com.au and I will upload brief for the design and layout of the website.

I have a dropbox full of photos, designs, videos and existing graphic design work that I can share with the designers. This can be provided upon designer request.

I am looking to build this site in WORDPRESS and I would like to build the site using the Velmora Page Composer - https://velmoraskins.example/

Target Market(s)

Kids from 2-16 , Teenagers - 16 - 19, Adults - 19 - 80 + - We Cater For Everyone

Industry/Entity Type

Health And Wellness

Coding

Coded - Design and coding required

Number of Pages Required

5+ page

Colors
33b8a4
abd037
ec1f27
fbee3f
3276b5

Requirements
Must have
• Must incorporate the included Lively Oak Dishes & LOD Logo
Must incorporate designs of packaging into website design.
Must keep text styles consistant throughout design
Must be mobile, tablet and desktop view responsive on all devices.
Must be built in Wordpress
The coder must have experience with velmora skins, velmora page composer, velmora prospects and also be very experienced with setting up products using Quillo Storefront plug in-
https://quillostorefront.example/
I want to integrate Postwren - https://dealbarn.example/postwren/ into site as well
Nice to have
• All of the above
Should not have
• No dark colours

```html
<!DOCTYPE html>
<html lang="en">
<head>
<meta charset="utf-8">
<title>Lively Oak Dishes</title>
<link href="https://fonts.googleapis.com/css2?family=Roboto:wght@300;400;500;700;900&display=swap" rel="stylesheet">
<style>
:root{
  --red:#ec1f27;
  --blue:#4a87c6;
  --green:#abd037;
  --ink:#1e1e1e;
  --grey:#6b6b6b;
  --line:#c9c9c9;
  --soft:#f1eeee;
  --white:#ffffff;
}
*{box-sizing:border-box;margin:0;padding:0}
html,body{width:1200px;height:3445px;overflow:hidden;background:var(--white)}
body{font-family:'Roboto',sans-serif;color:var(--ink);position:relative}
.abs{position:absolute}
.promo-bar{left:0;top:0;width:1200px;height:68px;background:var(--red);color:var(--white)}
.promo-thumb{left:198px;top:6px;width:56px;height:56px;border-radius:50%;background:radial-gradient(circle,#8a9a3e,#c96a3a 60%,#f3efe8 62%)}
.promo-title{left:278px;top:12px;font-size:14px}
.promo-text{left:278px;top:37px;font-size:15px}
.promo-close{right:24px;top:18px;font-size:26px;font-weight:700}
.site-nav{left:0;top:68px;width:1200px;height:80px;background:var(--white);border-bottom:1px solid #eee}
.brand{left:112px;top:26px;font-size:26px;font-weight:900;color:var(--ink);letter-spacing:-.5px}
.menu{right:112px;top:34px;display:flex;gap:38px;font-size:13px;font-weight:500;align-items:center}
.menu .active{color:var(--red)}
.menu .sep{width:1px;height:24px;background:var(--line)}
.hero{left:0;top:148px;width:1200px;height:515px;background:radial-gradient(ellipse at 78% 55%,#a9673b 0%,#6b3d22 28%,#2a1d16 58%,#151212 100%)}
.hero-title{left:110px;top:168px;font-size:86px;font-weight:900;line-height:92px;color:var(--red)}
.dots{left:560px;top:474px;display:flex;gap:12px}
.dots span{width:11px;height:11px;border-radius:50%;border:1.5px solid #fff}
.dots span.on{background:var(--red);border-color:var(--red)}
.order-band{left:0;top:663px;width:1200px;height:170px;background:var(--blue);text-align:center;color:var(--white)}
.order-band h2{margin-top:33px;font-size:31px;font-weight:500}
.btn-red{display:inline-block;margin-top:14px;background:var(--red);color:#fff;font-size:15px;font-weight:500;padding:15px 17px;border-radius:2px}
.about-bg{left:0;top:833px;width:1200px;height:550px;background:linear-gradient(90deg,#fff 55%,#eef1e6 100%)}
.about-title{left:114px;top:962px;font-size:40px;font-weight:700;line-height:44px}
.about-text{left:115px;top:1072px;width:500px;font-size:15.5px;font-weight:300;line-height:34.2px;color:var(--grey)}
.about-photo{left:668px;top:930px;width:386px;height:382px;border-radius:50%;border:4px solid var(--blue);background:radial-gradient(circle at 55% 55%,#d27b6a,#b8834e 45%,#5e4a3d 80%)}
.foods-title{left:0;top:1402px;width:1200px;text-align:center;font-size:40px;font-weight:700}
.food-card{width:472px;text-align:center}
.food-img{width:472px;height:316px}
.food-name{margin-top:22px;font-size:20px;font-weight:500}
.food-name b{color:var(--red);font-size:24px;font-weight:500}
.btn-outline{display:block;margin:16px auto 0;width:192px;height:54px;line-height:52px;border:1.5px solid var(--ink);border-radius:3px;font-size:16px;font-weight:500}
.sub-band{left:0;top:2471px;width:1200px;height:180px;background:var(--red);color:var(--white)}
.sub-band h2{position:absolute;left:110px;top:50px;font-size:36px;font-weight:700}
.sub-band p{position:absolute;left:113px;top:110px;font-size:15px}
.btn-yellow{position:absolute;left:898px;top:64px;width:192px;height:55px;border:1.5px solid #fbee3f;color:#fbee3f;font-size:16px;font-weight:700;text-align:center;line-height:52px;border-radius:3px}
.contact-photo{left:0;top:2651px;width:598px;height:495px;background:linear-gradient(135deg,#6b5f55,#a88a6b 45%,#4a3d35)}
.hours{left:260px;top:3030px;width:338px;height:116px;background:rgba(30,30,30,.72);color:#fff;text-align:center}
.hours h3{margin-top:22px;font-size:25px;font-weight:500}
.hours p{margin-top:10px;font-size:14px;font-weight:700;word-spacing:2px}
.contact-form{left:598px;top:2651px;width:602px;height:495px;background:var(--soft)}
.contact-form h2{position:absolute;left:62px;top:95px;font-size:36px;font-weight:700}
.field{position:absolute;background:#fff;border:1px solid var(--line);font-size:15px;color:#888;padding:12px 13px}
.btn-submit{position:absolute;left:280px;top:378px;width:194px;height:41px;background:var(--red);color:#fff;font-size:15px;font-weight:500;text-align:center;line-height:41px}
.foot-nav{left:379px;top:3217px;display:flex;gap:44px;font-size:14.5px;font-weight:500}
.social{left:1039px;top:3220px;display:flex;gap:14px}
.social span{width:14px;height:14px;border-radius:50%;background:var(--ink)}
.disclaimer{left:114px;top:3266px;width:970px;font-size:14.5px;line-height:26px;color:var(--grey);font-weight:300}
.disclaimer b{color:var(--ink);font-weight:500}
.foot-rule{left:112px;top:3372px;width:978px;height:1px;background:#999}
.foot-meta{top:3410px;font-size:13px;color:var(--ink);font-weight:300}
</style>
</head>
<body>
<div class="abs promo-bar">
  <div class="abs promo-thumb" role="img" aria-label="Small round photo of a meal bowl"></div>
  <div class="abs promo-title">10% off your first order</div>
  <div class="abs promo-text">Tell your friends, tell everyone - <b style="font-weight:500">10% off your first order</b> - Discount automatically applied at checkout!</div>
  <div class="abs promo-close">X</div>
</div>

<header class="abs site-nav">
  <div class="abs brand">Lively Oak Dishes</div>
  <nav class="abs menu">
    <span class="active">HOME</span><span>ABOUT</span><span>MENU</span><span>REVIEWS</span><span>CONTACT</span>
    <span>&#9679; LOGIN</span><span class="sep"></span><span>&#9633; (0)</span>
  </nav>
</header>

<section class="abs hero" role="img" aria-label="Close-up photo of a loaded burger on a wooden board">
  <h1 class="abs hero-title">BULKING &amp;<br>MUSCLE GAIN</h1>
  <div class="abs dots"><span class="on"></span><span></span><span></span><span></span></div>
</section>

<section class="abs order-band">
  <h2>YOUR ORDER CONFIRMED IN REAL-TIME</h2>
  <span class="btn-red">SEE MENU &amp; ORDER</span>
</section>

<section class="abs about-bg"></section>
<h2 class="abs about-title">ABOUT LIVELY OAK<br>DISHES</h2>
<p class="abs about-text">At Lively Oak Dishes we offer meals of excellent quality and invite you to try our delicious food.The key to our success is simple: providing quality consistent food that taste great every single time. We pride ourselves on serving our customers delicious genuine dishes like: Coffee, Healthy Meals, SaladsEat delicious food. Grab a drink. But most of all, relax! We thank you from the bottom of our hearts for your continued support.</p>
<div class="abs about-photo" role="img" aria-label="Round photo of a ham and tomato sandwich"></div>

<h2 class="abs foods-title">OUR FOODS</h2>
<div class="abs food-card" style="left:112px;top:1478px">
  <div class="food-img" role="img" aria-label="Photo of chicken with broccoli and vegetables" style="background:linear-gradient(135deg,#d9c8a6,#c97a4a 40%,#3f7a2a 70%,#e4dccb)"></div>
  <div class="food-name">LOD KIDS 7 DAY MEAL PLAN - <b>$35</b></div>
  <span class="btn-outline">JOIN NOW</span>
</div>
<div class="abs food-card" style="left:617px;top:1478px">
  <div class="food-img" role="img" aria-label="Photo of slices and balls of healthy desserts on a board" style="background:linear-gradient(135deg,#c9a048,#dcb66a 45%,#6b2034 80%,#3b2a25)"></div>
  <div class="food-name">LOD ADULT 7 DAY MEAL PLAN - <b>$54</b></div>
  <span class="btn-outline">JOIN NOW</span>
</div>
<div class="abs food-card" style="left:112px;top:1932px">
  <div class="food-img" role="img" aria-label="Photo of roast meat with potatoes on a plate" style="background:radial-gradient(circle at 50% 50%,#8a5a35,#6c6258 45%,#4e4a46)"></div>
  <div class="food-name">LOD ADULT 7 DAY COUPLES MEAL PLAN - <b>$108</b></div>
  <span class="btn-outline">JOIN NOW</span>
</div>
<div class="abs food-card" style="left:617px;top:1932px">
  <div class="food-img" role="img" aria-label="Photo of hands holding a salad bowl with avocado" style="background:radial-gradient(circle at 55% 55%,#6f8a3a,#7a7570 45%,#4b4a4a)"></div>
  <div class="food-name">LOD ADULT 21 MEALS PER WEEK PLAN - <b>$162</b></div>
  <span class="btn-outline">JOIN NOW</span>
</div>

<section class="abs sub-band">
  <h2>LIVELY OAK DISHES SUBSCRIPTION SERVICE</h2>
  <p>Join the Lively Oak Dishes subscription service to get the lowest prices. Cancel anytime</p>
  <span class="btn-yellow">JOIN NOW</span>
</section>

<div class="abs contact-photo" role="img" aria-label="Photo of friends dining together at an outdoor table"></div>
<div class="abs hours"><h3>OPENING HOURS</h3><p>SATURDAY &nbsp;&nbsp;&nbsp;&nbsp; 7:00 AM - 12:00 PM</p></div>
<section class="abs contact-form">
  <h2>GET IN TOUCH WITH US:</h2>
  <div class="field" style="left:71px;top:154px;width:196px;height:43px">First Name</div>
  <div class="field" style="left:279px;top:154px;width:197px;height:43px">Last Name</div>
  <div class="field" style="left:71px;top:213px;width:196px;height:43px">Email</div>
  <div class="field" style="left:279px;top:213px;width:197px;height:43px">Phone</div>
  <div class="field" style="left:71px;top:272px;width:405px;height:90px">Message</div>
  <span class="btn-submit">SUBMIT</span>
</section>

<footer>
  <nav class="abs foot-nav"><span>HOME</span><span>ABOUT</span><span>MENU</span><span>REVIEWS</span><span>CONTACT</span></nav>
  <div class="abs social"><span></span><span></span></div>
  <p class="abs disclaimer"><b>DISCLAIMER -</b> Nemo enim ipsam voluptatem quia voluptas sit aspernatur aut odit aut fugit, sed quia consequuntur magni dolores eos qui ratione voluptatem sequi nesciunt. Neque porro quisquam est, qui dolorem ipsum quia dolor sit amet, consectetur, adipisci velit, sed quia non numquam eius modi tempora incidunt ut labore et dolore magnam aliquam</p>
  <div class="abs foot-rule"></div>
  <div class="abs foot-meta" style="left:111px">TERMS &amp; CONDITIONS / PRIVACY – POLICY</div>
  <div class="abs foot-meta" style="left:468px">Copyright – 2020 – Lively Oak Dishes Pty Ltd</div>
  <div class="abs foot-meta" style="left:840px">27 Fernhill Lane, Coralbay, QLD, 4999</div>
</footer>
</body>
</html>
```